Präsentationsvorlagen für Immobilienvertrieb
Zielgruppe
Wir sind ein Immobilienvertrieb im Bereich Neubau- und Bestandsimmobilien aus München. Die Firma LORB existiert seit über 30 Jahren. Vor 5 Jahren haben wir ein cooles modernes Rebranding durchgeführt, sodass man mit unserem neuen Corporate Design richtig Spaß am Gestalten haben kann.
Eine konkrete Zielgruppe zu definieren ist schwierig, da unsere Käufer von 20-80 Jahren sein können. Ob junge, erfolgreiche Menschen, junge Familien, ältere Erwachsene, die von sich nach Auszug ihrer Kinder von ihrem Haus trennen wollen und eine kleinere Wohnung suchen oder einfach der Kapitalanleger, der auf der Suche nach einer neuen Investition ist.
Unsere CI ist gradlinig und setzt sich aus anthrazit, neonorange und weiß zusammen.
Im Bestand gibt es nicht pro Objekt ein CI, hier wird mit dem der LORB gearbeitet.
Im Neubau hat jedes einzelne Projekt sein eigenes CI (siehe aktuell hausfindel.de).
www.lorb.de
Aufgabenstellung
Zur Aufgabe: Für sowohl interne als auch externe Präsentationen benötigen wir eine firmeneinheitliche PowerPoint-Präsentationsvorlage, die sich wandelbar und modern von 'normalen' Präsentationen abhebt.
Vorgaben:
- CI der LORB muss verwendet werden (CI-Styleguide anbei)
- ansonsten sind der Kreativität keine Grenzen gesetzt
Die derzeitige Vorlage ist anbei.

```html
<!DOCTYPE html>
<html lang="de">
<head>
<meta charset="utf-8">
<title>LORB – Präsentationsvorlage</title>
<link rel="stylesheet" href="https://fonts.googleapis.com/css2?family=Montserrat:wght@300;400;600;700;800&display=swap">
<style>
:root{
  --orange:#e8461e;
  --orange-soft:#f0603a;
  --anthracite:#2b2b2c;
  --anthracite-2:#3a3a3b;
  --paper:#e8e9ea;
  --grey:#6b6b6b;
  --stage:#e5e2e1;
  --white:#ffffff;
}
*{margin:0;padding:0;box-sizing:border-box}
html,body{width:1200px;height:2585px;overflow:hidden;background:var(--white)}
body{font-family:'Montserrat',Arial,sans-serif;position:relative}
.stage{position:absolute;left:0;top:0;width:1200px;height:1330px;background:var(--stage)}
.s{position:absolute;width:210px;height:118px;background:var(--paper);overflow:hidden;color:var(--anthracite)}
.s>*{position:absolute}
.big{transform:scale(1.714);transform-origin:0 0;box-shadow:0 3px 8px rgba(0,0,0,.12)}
.dark{background:var(--anthracite);color:var(--white)}
.ph{display:block}
.mk{top:5px;right:5px;width:7px;height:7px;border:.6px solid #8a8a8a}
.ft{left:8px;right:8px;bottom:5px;height:.5px;background:var(--orange)}
.ft::after{content:"";position:absolute;right:30px;top:-.6px;width:12px;height:1.6px;background:var(--orange)}
.url{right:8px;bottom:7px;font-size:2.3px;color:#8a8a8a}
.h{font-weight:700;font-size:7.5px;letter-spacing:.4px;text-transform:uppercase;line-height:1.1}
.hl{font-weight:400;font-size:7.5px;letter-spacing:.6px;text-transform:uppercase;line-height:1.1}
.o{color:var(--orange)}
.w{color:var(--white)}
.p{font-size:2.6px;line-height:1.35;color:var(--grey)}
.pw{font-size:2.6px;line-height:1.35;color:#d6d6d6}
.bar{width:12px;height:1.2px;background:var(--orange)}
.num{font-size:8px;font-weight:400}
.box{background:var(--anthracite)}
.btn{height:6px;background:var(--anthracite);color:#fff;font-size:2.4px;text-align:center;line-height:6px;letter-spacing:.3px}
.circle{border-radius:50%}
.lbl{font-size:2.6px;font-weight:700;letter-spacing:.3px;color:var(--orange);text-transform:uppercase}
.brand{font-weight:700;letter-spacing:1px;color:var(--white)}
.brand-sq{background:var(--white)}
</style>
</head>
<body>

<div class="stage">

  <!-- Titel -->
  <div class="s dark big" style="left:30px;top:60px">
    <div class="ph" role="img" aria-label="Moderne Villa mit Bäumen in der Dämmerung" style="left:0;top:0;width:210px;height:118px;background:linear-gradient(120deg,#3c3f3e,#2a2d2c 60%,#4a4a45)"></div>
    <span class="h o" style="left:16px;top:40px;font-size:11px;font-weight:800">Herzblut<br>trifft<br>Immobilien</span>
    <p class="pw" style="left:16px;top:82px;width:90px">Immobilien im Bestand und im Neubau. Visionen und Lösungen – immer am Puls der Zeit.</p>
    <span class="brand" style="right:14px;top:16px;font-size:7px">LORB</span>
    <i class="brand-sq" style="right:46px;top:18px;width:5px;height:5px"></i>
    <i class="circle" style="left:16px;top:96px;width:12px;height:12px;border:.5px solid var(--orange)"></i>
  </div>

  <!-- Tradition -->
  <div class="s big" style="left:420px;top:60px">
    <div class="ph" role="img" aria-label="Tablet mit Bild eines modernen Wohnhauses" style="left:40px;top:6px;width:42px;height:62px;border-radius:3px;background:linear-gradient(160deg,#555,#222)"></div>
    <div class="box" style="left:14px;top:28px;width:60px;height:26px"></div>
    <span class="h o" style="left:18px;top:31px;font-size:6px">Tradition.<br>Innovation.<br>Motivation.</span>
    <span class="lbl" style="left:122px;top:14px">Innovation</span>
    <p class="p" style="left:122px;top:18px;width:70px">Kurzer Text zu unserem Anspruch und Angebot.</p>
    <span class="lbl" style="left:122px;top:34px">Motivation</span>
    <p class="p" style="left:122px;top:38px;width:70px">Kurzer Text zu unserem Anspruch und Angebot.</p>
    <i class="ft"></i><span class="url">www.lorb.de</span>
  </div>

  <!-- Agenda -->
  <div class="s big" style="left:810px;top:60px">
    <span class="hl" style="left:16px;top:16px">Agenda <b>23 / 24</b></span>
    <i class="circle" style="left:16px;top:36px;width:32px;height:32px;background:var(--orange)"></i><span class="w" style="left:24px;top:49px;font-size:5px;font-weight:700">2017</span>
    <i class="circle" style="left:62px;top:36px;width:32px;height:32px;border:.5px solid #555"></i><span style="left:70px;top:49px;font-size:5px">2019</span>
    <i class="circle" style="left:110px;top:30px;width:32px;height:32px;background:var(--orange)"></i><span class="w" style="left:118px;top:43px;font-size:5px;font-weight:700">2020</span>
    <i class="circle" style="left:156px;top:30px;width:32px;height:32px;border:.5px solid #555"></i><span style="left:164px;top:43px;font-size:5px">2023</span>
    <p class="p" style="left:26px;top:84px;width:90px">Kurzer Text zur Agenda und zu den nächsten Schritten im Jahr.</p>
    <i class="ft"></i><span class="url">www.lorb.de</span>
  </div>

  <!-- Find your best -->
  <div class="s big" style="left:30px;top:360px">
    <span class="hl" style="left:16px;top:18px">Find your best<br><b>real estate</b></span>
    <span class="lbl" style="left:28px;top:48px">Standort</span><p class="p" style="left:28px;top:52px;width:60px">Kurzer Text zum Standort.</p>
    <span class="lbl" style="left:28px;top:62px">Immobilientyp</span><p class="p" style="left:28px;top:66px;width:60px">Kurzer Text zum Objekttyp.</p>
    <span class="lbl" style="left:28px;top:76px">Preiskategorie</span><p class="p" style="left:28px;top:80px;width:60px">Kurzer Text zum Preis.</p>
    <i style="left:150px;top:14px;width:46px;height:72px;background:var(--orange)"></i>
    <div class="ph" role="img" aria-label="Illustration eines Hauses" style="left:118px;top:30px;width:56px;height:44px;background:linear-gradient(160deg,#f2f2f2,#a9b0b6)"></div>
    <i class="ft"></i><span class="url">www.lorb.de</span>
  </div>

  <!-- Leistung+X -->
  <div class="s dark big" style="left:420px;top:360px">
    <div class="ph" role="img" aria-label="Dunkles Esszimmer mit Bildern an der Wand" style="left:0;top:0;width:210px;height:118px;background:linear-gradient(110deg,#3a3a3a,#232323 55%,#444)"></div>
    <span class="num o" style="left:14px;top:18px">03.</span>
    <span class="h w" style="left:14px;top:30px">Leistung+X</span>
    <i class="bar" style="left:14px;top:42px"></i>
    <i class="circle" style="left:118px;top:32px;width:44px;height:44px;border:1px solid var(--orange)"></i>
    <p class="pw" style="left:14px;top:92px;width:80px">Kurzer Text zu unseren Leistungen und Services.</p>
    <i class="mk"></i>
  </div>

  <!-- Table of content -->
  <div class="s big" style="left:810px;top:360px">
    <span class="hl" style="left:16px;top:16px">Table of <b>content</b></span>
    <span class="lbl" style="left:16px;top:34px">01. Neubauprojekte</span><p class="p" style="left:16px;top:38px;width:110px">Kurzer Text zu unseren Neubauprojekten in München.</p>
    <span class="lbl" style="left:16px;top:50px">02. Bestandsimmobilien</span><p class="p" style="left:16px;top:54px;width:110px">Kurzer Text zu unseren Bestandsimmobilien in München.</p>
    <span class="lbl" style="left:16px;top:66px">03. Leistung+X</span><p class="p" style="left:16px;top:70px;width:110px">Kurzer Text zu unseren Leistungen und Services.</p>
    <i class="ft"></i><span class="url">www.lorb.de</span>
  </div>

  <!-- News website -->
  <div class="s big" style="left:30px;top:660px">
    <i class="box" style="left:0;top:14px;width:120px;height:90px"></i>
    <span class="hl w" style="left:14px;top:30px">News<br><b class="o">Website</b></span>
    <p class="pw" style="left:14px;top:56px;width:80px">Kurzer Text zu unserer neuen Website und den aktuellen Neuigkeiten für Sie.</p>
    <div class="ph" role="img" aria-label="Laptop mit Website und Stadtansicht" style="left:92px;top:34px;width:90px;height:54px;border-radius:2px;background:linear-gradient(160deg,#8a8d90,#3b3b3b)"></div>
    <i class="ft"></i><span class="url">www.lorb.de</span>
  </div>

  <!-- Mit Substanz -->
  <div class="s big" style="left:420px;top:660px">
    <div class="ph" role="img" aria-label="Fassade mit bunten Lamellen" style="left:0;top:8px;width:70px;height:40px;background:linear-gradient(90deg,#d8452b,#333,#c7c7c7,#e56a3f)"></div>
    <div class="ph" role="img" aria-label="Hochhaus vor blauem Himmel" style="left:0;top:52px;width:60px;height:50px;background:linear-gradient(160deg,#4f86c5,#8a3a2a)"></div>
    <div class="ph" role="img" aria-label="Helle Architektur mit orangem Detail" style="left:64px;top:60px;width:52px;height:42px;background:linear-gradient(140deg,#f3f3f3,#e57a3a)"></div>
    <div class="ph" role="img" aria-label="Modernes Badezimmer" style="left:120px;top:56px;width:50px;height:46px;background:linear-gradient(140deg,#a8a8a8,#505050)"></div>
    <span class="hl" style="left:82px;top:16px"><b>Mit Substanz</b><br>Immobilienverkauf</span>
    <p class="p" style="left:82px;top:36px;width:110px">Kurzer Text zum Verkauf Ihrer Immobilie mit Erfahrung und Substanz.</p>
    <i class="ft"></i><span class="url">www.lorb.de</span>
  </div>

  <!-- Chart -->
  <div class="s big" style="left:810px;top:660px">
    <svg style="left:20px;top:14px" width="170" height="86" viewBox="0 0 170 86">
      <rect x="10" y="30" width="8" height="56" fill="#e8461e"/><rect x="20" y="44" width="8" height="42" fill="#2b2b2c"/><rect x="30" y="52" width="8" height="34" fill="#8a8a8a"/>
      <rect x="60" y="14" width="8" height="72" fill="#e8461e"/><rect x="70" y="38" width="8" height="48" fill="#2b2b2c"/><rect x="80" y="48" width="8" height="38" fill="#8a8a8a"/>
      <rect x="110" y="4" width="8" height="82" fill="#e8461e"/><rect x="120" y="24" width="8" height="62" fill="#2b2b2c"/><rect x="130" y="36" width="8" height="50" fill="#8a8a8a"/>
    </svg>
  </div>

  <!-- Kontakt -->
  <div class="s dark big" style="left:30px;top:960px">
    <div class="ph" role="img" aria-label="Park mit Bäumen und Turm im Hintergrund" style="left:0;top:0;width:210px;height:118px;background:linear-gradient(120deg,#3e4a3c,#2b2d2b 60%,#333)"></div>
    <span class="h w" style="left:14px;top:22px">Kontakt</span><i class="bar" style="left:14px;top:32px"></i>
    <p class="pw" style="left:14px;top:40px;width:80px">Kurzer Text zur Kontaktaufnahme mit unserem Team in München.</p>
    <span class="lbl" style="left:14px;top:78px">Neubauprojekte</span>
    <p class="pw" style="left:14px;top:82px;width:70px">LORB Neubau GmbH<br>Hofgut Am Weiher 3<br>85640 Lindenfeld</p>
    <span class="lbl" style="left:100px;top:72px">Bestehende Immobilien</span>
    <p class="pw" style="left:100px;top:76px;width:70px">LORB Immobilien GmbH<br>Kastanienallee 118<br>80799 München</p>
    <span class="brand" style="right:14px;top:16px;font-size:7px">LORB</span>
    <i class="brand-sq" style="right:46px;top:18px;width:5px;height:5px"></i>
  </div>

  <!-- 04 bewerten -->
  <div class="s big" style="left:420px;top:960px;background:var(--orange)">
    <div class="ph" role="img" aria-label="Orange Fassadenlamellen" style="left:80px;top:0;width:130px;height:118px;background:linear-gradient(90deg,#e8461e,#d63c18 40%,#2b2b2c 80%,#c9c9c9)"></div>
    <span class="num w" style="left:14px;top:18px">04.</span>
    <span class="h w" style="left:14px;top:30px">Immobilie<br>bewerten</span>
    <i style="left:14px;top:50px;width:12px;height:1.2px;background:#fff"></i>
    <p class="pw" style="left:14px;top:92px;width:80px;color:#fff">Kurzer Text zur Bewertung Ihrer Immobilie durch unser Team.</p>
    <i class="mk" style="border-color:#fff"></i>
  </div>

  <!-- Immobilien Wissen -->
  <div class="s big" style="left:810px;top:960px">
    <div class="ph" role="img" aria-label="Drei Innenraumfotos von Wohnungen" style="left:0;top:8px;width:210px;height:50px;background:linear-gradient(90deg,#c9c9c9,#8a7d6c 40%,#d8c3a8 70%,#6f5a45)"></div>
    <i class="box" style="left:16px;top:52px;width:60px;height:22px"></i>
    <span class="hl w" style="left:20px;top:56px">Immobilien<br><b class="o">Wissen</b></span>
    <p class="p" style="left:84px;top:64px;width:110px">Kurzer Text mit Wissen rund um Kauf, Verkauf und Bewertung.</p>
    <i class="ft"></i><span class="url">www.lorb.de</span>
  </div>
</div>

<!-- ===== Übersicht aller Folien ===== -->

<!-- Reihe 1 -->
<div class="s" style="left:48px;top:1405px;background:linear-gradient(90deg,#d7392b,#ea5140)">
  <div class="ph" role="img" aria-label="Rote Haustür an heller Wand" style="left:92px;top:30px;width:36px;height:70px;background:#c97a43"></div>
  <span class="num" style="left:14px;top:14px;color:#f7a58d">01.</span><span class="h w" style="left:14px;top:28px">Neubauprojekte</span>
  <p class="pw" style="left:14px;top:94px;width:80px;color:#fff">Kurzer Text zu unseren aktuellen Neubauprojekten.</p>
  <i class="mk" style="border-color:#f5b3a0"></i>
</div>
<div class="s" style="left:272px;top:1405px;background:var(--orange)">
  <div class="ph" role="img" aria-label="Orange Fassadenlamellen" style="left:80px;top:0;width:130px;height:118px;background:linear-gradient(90deg,#e8461e,#d13d17,#ef6a42)"></div>
  <span class="num w" style="left:14px;top:14px">02.</span><span class="h w" style="left:14px;top:26px">Bestands-<br>immobilien</span>
  <p class="pw" style="left:14px;top:94px;width:80px;color:#fff">Kurzer Text zu unseren Bestandsimmobilien.</p>
  <i class="mk" style="border-color:#fff"></i>
</div>
<div class="s dark" style="left:496px;top:1405px">
  <div class="ph" role="img" aria-label="Dunkles Esszimmer" style="left:0;top:0;width:210px;height:118px;background:linear-gradient(110deg,#3a3a3a,#242424,#444)"></div>
  <span class="num o" style="left:14px;top:14px">03.</span><span class="h w" style="left:14px;top:28px">Leistung+X</span>
  <i class="circle" style="left:120px;top:30px;width:40px;height:40px;border:1px solid var(--orange)"></i>
  <p class="pw" style="left:14px;top:94px;width:80px">Kurzer Text zu unseren Leistungen.</p><i class="mk"></i>
</div>
<div class="s" style="left:720px;top:1405px;background:var(--orange)">
  <div class="ph" role="img" aria-label="Orange Fassadenlamellen" style="left:80px;top:0;width:130px;height:118px;background:linear-gradient(90deg,#e8461e,#d63c18 55%,#2b2b2c 85%,#c9c9c9)"></div>
  <span class="num w" style="left:14px;top:14px">04.</span><span class="h w" style="left:14px;top:26px">Immobilie<br>bewerten</span>
  <p class="pw" style="left:14px;top:94px;width:80px;color:#fff">Kurzer Text zur Bewertung Ihrer Immobilie.</p><i class="mk" style="border-color:#fff"></i>
</div>
<div class="s dark" style="left:944px;top:1405px">
  <div class="ph" role="img" aria-label="Team bei der Besprechung im Büro" style="left:0;top:0;width:210px;height:118px;background:linear-gradient(110deg,#2f2f2f,#4a4744,#2b2b2b)"></div>
  <span class="num o" style="left:14px;top:14px">05.</span><span class="h w" style="left:14px;top:26px">Wer wir<br>sind</span>
  <p class="pw" style="left:14px;top:94px;width:80px">Kurzer Text über unser Team und uns.</p><i class="mk"></i>
</div>

<!-- Reihe 2 -->
<div class="s" style="left:48px;top:1543px">
  <div class="ph" role="img" aria-label="Helles Wohnzimmer mit Kajak an der Wand" style="left:92px;top:0;width:100px;height:88px;background:linear-gradient(140deg,#d8c8b0,#9a7b58)"></div>
  <span class="hl" style="left:14px;top:18px">Hello!<br><b class="o">Welcome</b></span>
  <i class="box" style="left:0;top:52px;width:84px;height:44px"></i>
  <p class="pw" style="left:12px;top:58px;width:66px">Kurzer Text zur Begrüßung und zu unserem Team in München.</p>
  <i class="mk"></i><i class="ft"></i>
</div>
<div class="s" style="left:272px;top:1543px">
  <div class="ph" role="img" aria-label="Collage aus Architekturdetails" style="left:0;top:14px;width:100px;height:86px;background:linear-gradient(135deg,#b3402d,#6b5a48,#c9a36e,#8a3c6a)"></div>
  <i class="box" style="left:100px;top:0;width:42px;height:40px"></i>
  <p class="pw" style="left:104px;top:10px;width:34px">Kurzer Text zur Einleitung.</p>
  <span class="h o" style="left:148px;top:20px;font-size:5.5px;font-weight:400">Aus<br>Liebe zum<br><b>Bestehen-<br>den</b></span>
  <p class="p" style="left:148px;top:56px;width:52px">Kurzer Text zu Bestand und Werterhalt.</p>
  <i class="mk"></i><i class="ft"></i>
</div>
<div class="s" style="left:496px;top:1543px">
  <div class="ph" role="img" aria-label="Bunte Fassade aus Lamellen" style="left:8px;top:0;width:96px;height:104px;background:linear-gradient(90deg,#2b2b2c,#e8461e,#444,#e8461e)"></div>
  <span class="hl" style="left:114px;top:16px;font-size:5.5px"><b>Immobilien</b> als<br>Kapitalanlage</span>
  <i class="box" style="left:108px;top:40px;width:102px;height:58px"></i>
  <p class="pw" style="left:116px;top:48px;width:84px">Kurzer Text zur Immobilie als sichere Kapitalanlage für Ihre Zukunft.</p>
  <i class="mk"></i><i class="ft"></i>
</div>
<div class="s" style="left:720px;top:1543px">
  <span class="hl" style="left:14px;top:14px;font-size:5.5px">Was ist Ihre<br>Immobilie<br><b>wert?</b></span>
  <p class="p" style="left:14px;top:56px;width:80px">Kurzer Text zur Bewertung Ihrer Immobilie mit unserem Team.</p>
  <span class="btn" style="left:124px;top:20px;width:64px">Einfamilienhaus</span>
  <span class="btn" style="left:124px;top:42px;width:64px">Eigentumswohnung</span>
  <span class="btn" style="left:124px;top:62px;width:64px">Mehrfamilienhaus</span>
  <span class="btn" style="left:124px;top:84px;width:64px;background:var(--orange)">Online bewerten</span>
  <i class="mk"></i><i class="ft"></i>
</div>
<div class="s" style="left:944px;top:1543px">
  <div class="ph" role="img" aria-label="Porträt einer Mitarbeiterin" style="left:14px;top:18px;width:64px;height:82px;background:linear-gradient(160deg,#d7773b,#5a3d30)"></div>
  <span class="hl o" style="left:94px;top:20px;font-size:5.5px"><b>Gemeinsam</b> gewinnen</span>
  <i class="box" style="left:78px;top:30px;width:132px;height:42px"></i>
  <span class="o" style="left:100px;top:36px;font-size:3px;font-weight:700">Mara T. Lindholm</span>
  <p class="pw" style="left:100px;top:44px;width:90px">Kurzer Text zur Ansprechpartnerin und ihrer Aufgabe.</p>
  <span class="p" style="left:100px;top:82px">089 123 456 00</span><span class="p" style="left:160px;top:82px">info@lorb.de</span>
  <i class="mk"></i><i class="ft"></i>
</div>

<!-- Reihe 3 -->
<div class="s" style="left:48px;top:1680px">
  <i class="box" style="left:0;top:0;width:134px;height:100px"></i>
  <span class="hl w" style="left:14px;top:22px;font-size:5.5px">News<br><b class="o">Website</b></span>
  <p class="pw" style="left:14px;top:44px;width:66px">Kurzer Text zu unserer neuen Website und aktuellen Neuigkeiten.</p>
  <div class="ph" role="img" aria-label="Laptop mit Website" style="left:94px;top:28px;width:96px;height:56px;background:linear-gradient(160deg,#8a8d90,#3b3b3b)"></div>
  <i class="mk"></i><i class="ft"></i>
</div>
<div class="s" style="left:272px;top:1680px">
  <div class="ph" role="img" aria-label="Tablet mit Hausfoto" style="left:52px;top:10px;width:62px;height:94px;border-radius:4px;background:linear-gradient(160deg,#555,#222)"></div>
  <i class="box" style="left:14px;top:44px;width:58px;height:28px"></i>
  <span class="h o" style="left:18px;top:48px;font-size:5.5px">Tradition.<br>Innovation.<br>Motivation.</span>
  <span class="lbl" style="left:136px;top:24px">Tradition</span><p class="p" style="left:136px;top:28px;width:60px">Kurzer Text zur Tradition.</p>
  <span class="lbl" style="left:136px;top:48px">Innovation</span><p class="p" style="left:136px;top:52px;width:60px">Kurzer Text zur Innovation.</p>
  <span class="lbl" style="left:136px;top:72px">Motivation</span><p class="p" style="left:136px;top:76px;width:60px">Kurzer Text zur Motivation.</p>
  <i class="mk"></i><i class="ft"></i>
</div>
<div class="s" style="left:496px;top:1680px">
  <span class="hl" style="left:14px;top:18px;font-size:5.5px">Planen<br>mit der<br><b>LORB</b></span>
  <p class="p" style="left:14px;top:48px;width:70px">Kurzer Text zur Planung Ihres Projekts mit unserem Team.</p>
  <i class="box" style="left:88px;top:0;width:18px;height:18px"></i>
  <div class="ph" role="img" aria-label="Helles Treppenhaus" style="left:108px;top:20px;width:40px;height:80px;background:linear-gradient(160deg,#d8d8d8,#8a8a8a)"></div>
  <div class="ph" role="img" aria-label="Essbereich mit Holztisch" style="left:150px;top:20px;width:52px;height:38px;background:linear-gradient(160deg,#c9b08c,#6f5a45)"></div>
  <div class="ph" role="img" aria-label="Modernes Badezimmer" style="left:150px;top:60px;width:52px;height:40px;background:linear-gradient(160deg,#8a8a8a,#3f3f3f)"></div>
  <i class="mk"></i><i class="ft"></i>
</div>
<div class="s" style="left:720px;top:1680px">
  <span class="h" style="left:14px;top:16px;font-size:5.5px">Weitblick,<br>Fachwissen<br>und<br>Expertise.</span>
  <span class="lbl" style="left:14px;top:72px">Create something new with us</span>
  <p class="p" style="left:14px;top:78px;width:64px">Kurzer Text zu unserem Wissen.</p>
  <svg style="left:88px;top:20px" width="110" height="80" viewBox="0 0 110 80">
    <g fill="#e8461e"><rect x="0" y="0" width="25" height="5"/><rect x="27" y="0" width="25" height="5"/><rect x="54" y="0" width="25" height="5"/><rect x="81" y="0" width="25" height="5"/></g>
    <g fill="#fff"><rect x="0" y="7" width="106" height="5"/><rect x="0" y="14" width="106" height="5"/><rect x="0" y="21" width="106" height="5"/><rect x="0" y="28" width="106" height="5"/><rect x="0" y="44" width="106" height="5"/><rect x="0" y="51" width="106" height="5"/><rect x="0" y="58" width="106" height="5"/></g>
    <g fill="#e8461e"><rect x="90" y="44" width="16" height="5"/><rect x="90" y="51" width="16" height="5"/><rect x="90" y="58" width="16" height="5"/></g>
  </svg>
  <i class="mk"></i><i class="ft"></i>
</div>
<div class="s" style="left:944px;top:1680px">
  <span class="hl o" style="left:74px;top:12px;font-size:5.5px">Unser Team</span>
  <i class="box" style="left:0;top:48px;width:210px;height:50px"></i>
  <div class="ph" role="img" aria-label="Porträt Mitarbeiter" style="left:22px;top:26px;width:36px;height:36px;background:#5a5a5a"></div>
  <div class="ph" role="img" aria-label="Porträt Mitarbeiterin" style="left:88px;top:26px;width:36px;height:36px;background:#6a6360"></div>
  <div class="ph" role="img" aria-label="Porträt Mitarbeiter" style="left:152px;top:26px;width:36px;height:36px;background:#4a4a4a"></div>
  <span class="lbl" style="left:24px;top:68px">Jonas Berg</span><span class="lbl" style="left:90px;top:68px">Lena Kurz</span><span class="lbl" style="left:154px;top:68px">Timo Rahn</span>
  <p class="pw" style="left:20px;top:74px;width:40px">Kurzer Text zur Person.</p><p class="pw" style="left:86px;top:74px;width:40px">Kurzer Text zur Person.</p><p class="pw" style="left:150px;top:74px;width:40px">Kurzer Text zur Person.</p>
  <i class="mk"></i><i class="ft"></i>
</div>

<!-- Reihe 4 -->
<div class="s" style="left:48px;top:1817px">
  <div class="ph" role="img" aria-label="Hausmodell mit Blumen neben Laptop" style="left:0;top:0;width:120px;height:100px;background:linear-gradient(140deg,#e4e0da,#b35a3a 60%,#d9d2c8)"></div>
  <i class="box" style="left:100px;top:0;width:20px;height:18px"></i>
  <span class="hl" style="left:128px;top:16px;font-size:5px">Introduction,<br><b class="o">we are</b></span>
  <p class="p" style="left:128px;top:32px;width:70px">Kurzer Text zur Einführung in unser Unternehmen und unsere Werte.</p>
  <i class="mk"></i><i class="ft"></i>
</div>
<div class="s" style="left:272px;top:1817px">
  <div class="ph" role="img" aria-label="Fassade mit bunten Lamellen" style="left:0;top:0;width:70px;height:40px;background:linear-gradient(90deg,#d8452b,#333,#c7c7c7,#e56a3f)"></div>
  <div class="ph" role="img" aria-label="Hochhaus vor Himmel" style="left:10px;top:44px;width:56px;height:56px;background:linear-gradient(160deg,#4f86c5,#8a3a2a)"></div>
  <div class="ph" role="img" aria-label="Helle Architektur" style="left:70px;top:56px;width:56px;height:44px;background:linear-gradient(140deg,#f3f3f3,#e57a3a)"></div>
  <div class="ph" role="img" aria-label="Badezimmer" style="left:130px;top:56px;width:56px;height:44px;background:linear-gradient(140deg,#a8a8a8,#505050)"></div>
  <span class="hl" style="left:78px;top:12px;font-size:5.5px"><b>Mit Substanz</b><br>Immobilienverkauf</span>
  <p class="p" style="left:78px;top:28px;width:110px">Kurzer Text zum Verkauf Ihrer Immobilie.</p>
  <i class="mk"></i><i class="ft"></i>
</div>
<div class="s" style="left:496px;top:1817px">
  <span class="hl" style="left:14px;top:14px;font-size:5.5px">Find your best<br><b>real estate</b></span>
  <span class="lbl" style="left:24px;top:40px">Standort</span><p class="p" style="left:24px;top:44px;width:60px">Kurzer Text zum Standort.</p>
  <span class="lbl" style="left:24px;top:56px">Immobilientyp</span><p class="p" style="left:24px;top:60px;width:60px">Kurzer Text zum Objekttyp.</p>
  <span class="lbl" style="left:24px;top:72px">Preiskategorie</span><p class="p" style="left:24px;top:76px;width:60px">Kurzer Text zum Preis.</p>
  <i style="left:152px;top:14px;width:44px;height:68px;background:var(--orange)"></i>
  <div class="ph" role="img" aria-label="Illustration eines Hauses" style="left:118px;top:30px;width:54px;height:42px;background:linear-gradient(160deg,#f2f2f2,#a9b0b6)"></div>
  <i class="mk"></i><i class="ft"></i>
</div>
<div class="s" style="left:720px;top:1817px">
  <span class="hl" style="left:14px;top:22px;font-size:5px">Aus<br>Leidenschaft<br>für <b class="o">Neues</b></span>
  <span class="lbl" style="left:14px;top:58px">Wir schaffen Neues</span>
  <p class="p" style="left:14px;top:64px;width:66px">Kurzer Text zu unseren Ideen.</p>
  <i class="box" style="left:86px;top:18px;width:52px;height:34px"></i><i class="box" style="left:144px;top:18px;width:52px;height:34px"></i>
  <i class="box" style="left:86px;top:58px;width:52px;height:34px"></i><i class="box" style="left:144px;top:58px;width:52px;height:34px"></i>
  <p class="pw" style="left:90px;top:36px;width:44px">Kurzer Text.</p><p class="pw" style="left:148px;top:36px;width:44px">Kurzer Text.</p>
  <p class="pw" style="left:90px;top:76px;width:44px">Kurzer Text.</p><p class="pw" style="left:148px;top:76px;width:44px">Kurzer Text.</p>
  <i class="mk"></i><i class="ft"></i>
</div>
<div class="s" style="left:944px;top:1817px">
  <span class="h" style="left:14px;top:16px;font-size:4.5px">Unsere<br>Projekt-<br>entwickler</span>
  <p class="p" style="left:14px;top:46px;width:70px">Kurzer Text zu unseren Projektentwicklern.</p>
  <div class="ph" role="img" aria-label="Mann mit Rucksack" style="left:92px;top:8px;width:30px;height:60px;background:linear-gradient(160deg,#c8c2bc,#6a3b2b)"></div>
  <div class="ph" role="img" aria-label="Büro mit Fensterfront" style="left:126px;top:30px;width:34px;height:40px;background:linear-gradient(160deg,#b8b4ae,#4a4a4a)"></div>
  <div class="ph" role="img" aria-label="Team im Gespräch" style="left:162px;top:36px;width:38px;height:60px;background:linear-gradient(160deg,#c9c4bd,#5a5652)"></div>
  <i class="mk"></i><i class="ft"></i>
</div>

<!-- Reihe 5 -->
<div class="s" style="left:48px;top:1954px">
  <i class="box" style="left:0;top:16px;width:98px;height:80px"></i>
  <span class="h o" style="left:14px;top:24px;font-size:5.5px">Hausfindel<br><span style="font-weight:400">München<br>West</span></span>
  <p class="pw" style="left:14px;top:50px;width:76px">Kurzer Text zum Neubauprojekt im Münchner Westen.</p>
  <div class="ph" role="img" aria-label="Weißes modernes Haus mit Garten" style="left:106px;top:16px;width:96px;height:80px;background:linear-gradient(160deg,#e8e8e8,#9ca59a)"></div>
  <i class="mk"></i><i class="ft"></i>
</div>
<div class="s" style="left:272px;top:1954px">
  <span class="h o" style="left:14px;top:14px;font-size:5.5px">Bereits<br><span style="font-weight:400;color:#2b2b2c">verkauft</span></span>
  <p class="p" style="left:14px;top:34px;width:60px">Kurzer Text zu bereits verkauften Objekten.</p>
  <div class="ph" role="img" aria-label="Dunkle Hausfassade vor blauem Himmel" style="left:80px;top:0;width:62px;height:110px;background:linear-gradient(160deg,#cfe0ef,#2c3b4a)"></div>
  <div class="ph" role="img" aria-label="Rote Fassade" style="left:146px;top:0;width:40px;height:110px;background:linear-gradient(160deg,#c02a1e,#6e1510)"></div>
  <svg style="left:128px;top:40px" width="30" height="16" viewBox="0 0 30 16"><path d="M1 8H27M20 1L28 8L20 15" stroke="#fff" stroke-width="2" fill="none"/></svg>
  <i class="mk"></i>
</div>
<div class="s" style="left:496px;top:1954px">
  <div class="ph" role="img" aria-label="Illustration eines spiralförmigen Trichters in Rot" style="left:14px;top:12px;width:52px;height:84px;background:linear-gradient(180deg,#e8461e,#b33a22 55%,#8a3a2a)"></div>
  <span class="h" style="left:102px;top:22px;font-size:5.5px">Verkauf<br>Kriterien</span>
  <span class="lbl" style="left:110px;top:44px">Development</span><span class="lbl" style="left:160px;top:44px">Foundation</span>
  <span class="lbl" style="left:110px;top:66px">Digital Tax</span><span class="lbl" style="left:160px;top:66px">Display Form</span>
  <p class="p" style="left:110px;top:50px;width:40px">Kurzer Text.</p><p class="p" style="left:160px;top:50px;width:40px">Kurzer Text.</p>
  <p class="p" style="left:110px;top:72px;width:40px">Kurzer Text.</p><p class="p" style="left:160px;top:72px;width:40px">Kurzer Text.</p>
  <i class="mk"></i><i class="ft"></i>
</div>
<div class="s" style="left:720px;top:1954px">
  <svg style="left:12px;top:20px" width="90" height="76" viewBox="0 0 90 76">
    <rect x="4" y="18" width="5" height="58" fill="#e8461e"/><rect x="10" y="34" width="5" height="42" fill="#2b2b2c"/><rect x="16" y="40" width="5" height="36" fill="#8a8a8a"/>
    <rect x="34" y="8" width="5" height="68" fill="#e8461e"/><rect x="40" y="30" width="5" height="46" fill="#2b2b2c"/><rect x="46" y="36" width="5" height="40" fill="#8a8a8a"/>
    <rect x="64" y="2" width="5" height="74" fill="#e8461e"/><rect x="70" y="22" width="5" height="54" fill="#2b2b2c"/><rect x="76" y="32" width="5" height="44" fill="#8a8a8a"/>
  </svg>
  <span class="hl" style="left:112px;top:22px;font-size:5px">Wir bewerten<br><b>Ihre Immobilie</b></span>
  <p class="p" style="left:112px;top:40px;width:84px">Kurzer Text zur Bewertung Ihrer Immobilie durch unsere Experten vor Ort.</p>
  <i class="mk"></i><i class="ft"></i>
</div>
<div class="s" style="left:944px;top:1954px">
  <span class="hl o" style="left:66px;top:10px;font-size:5px">Starke <b>Partner</b></span>
  <div class="ph" role="img" aria-label="Wohnanlage Partner A" style="left:14px;top:24px;width:28px;height:26px;background:#9aa09c"></div>
  <i class="box" style="left:44px;top:24px;width:52px;height:26px"></i><i class="circle" style="left:50px;top:28px;width:8px;height:8px;background:#fff"></i>
  <div class="ph" role="img" aria-label="Wohnanlage Partner B" style="left:108px;top:24px;width:28px;height:26px;background:#8e8a84"></div>
  <i class="box" style="left:138px;top:24px;width:56px;height:26px"></i><i style="left:176px;top:28px;width:12px;height:6px;background:#fff"></i>
  <div class="ph" role="img" aria-label="Wohnanlage Partner C" style="left:14px;top:62px;width:28px;height:26px;background:#8c9da8"></div>
  <i class="box" style="left:44px;top:62px;width:52px;height:26px"></i><i style="left:56px;top:66px;width:24px;height:5px;background:#fff"></i>
  <div class="ph" role="img" aria-label="Wohnanlage Partner D" style="left:108px;top:62px;width:28px;height:26px;background:#a5a09a"></div>
  <i class="box" style="left:138px;top:62px;width:56px;height:26px"></i><i style="left:176px;top:66px;width:12px;height:6px;background:#fff"></i>
  <i class="mk"></i><i class="ft"></i>
</div>

<!-- Reihe 6 -->
<div class="s" style="left:48px;top:2091px">
  <div class="ph" role="img" aria-label="Schlüssel mit Hausanhänger auf dunklem Grund" style="left:0;top:16px;width:116px;height:84px;background:linear-gradient(140deg,#3a3a3a,#8a3a22 60%,#2b2b2b)"></div>
  <i class="box" style="left:124px;top:16px;width:80px;height:22px"></i>
  <span class="hl w" style="left:130px;top:20px;font-size:5px">About our<br><b>business</b></span>
  <span class="lbl" style="left:128px;top:44px">01 Sales</span><p class="p" style="left:128px;top:48px;width:70px">Kurzer Text zum Vertrieb.</p>
  <span class="lbl" style="left:128px;top:60px">02 Services</span><p class="p" style="left:128px;top:64px;width:70px">Kurzer Text zum Service.</p>
  <span class="lbl" style="left:128px;top:76px">03 Before Fast</span><p class="p" style="left:128px;top:80px;width:70px">Kurzer Text zum Ablauf.</p>
  <i class="mk"></i><i class="ft"></i>
</div>
<div class="s" style="left:272px;top:2091px">
  <div class="ph" role="img" aria-label="Weiße Fassade mit Hausnummer" style="left:10px;top:10px;width:70px;height:54px;background:linear-gradient(160deg,#efefef,#a0a0a0)"></div>
  <div class="ph" role="img" aria-label="Moderne Fassade mit runden Balkonen" style="left:82px;top:56px;width:54px;height:48px;background:linear-gradient(160deg,#cfe0ef,#3b6ea5)"></div>
  <div class="ph" role="img" aria-label="Haus im Grünen" style="left:140px;top:34px;width:48px;height:30px;background:linear-gradient(160deg,#a8c6e0,#6a8a4a)"></div>
  <i class="box" style="left:84px;top:10px;width:48px;height:40px"></i>
  <span class="h w" style="left:88px;top:14px;font-size:4px">Immobilie<br>bewerten</span>
  <p class="pw" style="left:88px;top:26px;width:40px">Kurzer Text zur Bewertung.</p>
  <i class="box" style="left:158px;top:68px;width:18px;height:18px"></i>
  <i class="mk"></i><i class="ft"></i>
</div>
<div class="s" style="left:496px;top:2091px">
  <span class="h" style="left:14px;top:14px;font-size:5px">Buy and sell<br>your property<br>without<br>commisions</span>
  <p class="p" style="left:14px;top:44px;width:100px">Kurzer Text zu Kauf und Verkauf ohne zusätzliche Provision.</p>
  <span class="h" style="left:20px;top:72px;font-size:5px">78M</span><span class="h o" style="left:50px;top:72px;font-size:5px">89%</span><span class="h" style="left:84px;top:72px;font-size:5px">27K</span>
  <span class="p" style="left:20px;top:80px">Umsatz</span><span class="p" style="left:50px;top:80px">Kunden</span><span class="p" style="left:84px;top:80px">Objekte</span>
  <svg style="left:124px;top:24px" width="64" height="64" viewBox="0 0 64 64">
    <circle cx="32" cy="32" r="30" fill="#e8461e"/><path d="M32 32L32 2A30 30 0 0 0 5 45Z" fill="#2b2b2c"/><path d="M32 32L32 2A30 30 0 0 1 50 8Z" fill="#8a8a8a"/><circle cx="32" cy="32" r="7" fill="#fff"/>
  </svg>
  <i class="mk"></i><i class="ft"></i>
</div>
<div class="s" style="left:720px;top:2091px">
  <span class="h o" style="left:14px;top:14px;font-size:5px">Markt<br>Preis<br><span style="font-weight:400;color:#2b2b2c">Einschätzung</span></span>
  <i class="circle" style="left:16px;top:60px;width:4px;height:4px;background:#2b2b2c"></i><span class="p" style="left:24px;top:60px">Sehr zufrieden</span>
  <i class="circle" style="left:16px;top:72px;width:4px;height:4px;background:#8a8a8a"></i><span class="p" style="left:24px;top:72px">Zufrieden</span>
  <i class="circle" style="left:16px;top:84px;width:4px;height:4px;background:var(--orange)"></i><span class="p" style="left:24px;top:84px">Nicht zufrieden</span>
  <svg style="left:108px;top:14px" width="76" height="76" viewBox="0 0 76 76">
    <circle cx="38" cy="38" r="30" fill="none" stroke="#2b2b2c" stroke-width="9"/>
    <circle cx="38" cy="38" r="30" fill="none" stroke="#8a8a8a" stroke-width="9" stroke-dasharray="50 189" transform="rotate(200 38 38)"/>
    <circle cx="38" cy="38" r="30" fill="none" stroke="#e8461e" stroke-width="9" stroke-dasharray="34 189" transform="rotate(-90 38 38)"/>
    <circle cx="38" cy="38" r="13" fill="#fff"/><path d="M31 40L38 33L45 40V46H31Z" fill="none" stroke="#e8461e" stroke-width="1.5"/>
  </svg>
  <i class="mk"></i><i class="ft"></i>
</div>
<div class="s dark" style="left:944px;top:2091px">
  <div class="ph" role="img" aria-label="Park mit Bäumen" style="left:0;top:0;width:210px;height:118px;background:linear-gradient(120deg,#3e4a3c,#2b2d2b 60%,#333)"></div>
  <span class="h w" style="left:14px;top:16px;font-size:6px">Kontakt</span>
  <span class="lbl" style="left:14px;top:76px">Neubauprojekte</span>
  <p class="pw" style="left:14px;top:80px;width:60px">LORB Neubau GmbH<br>Hofgut Am Weiher 3<br>85640 Lindenfeld</p>
  <span class="lbl" style="left:82px;top:76px">Bestehende Immobilien</span>
  <p class="pw" style="left:82px;top:80px;width:60px">LORB Immobilien GmbH<br>Kastanienallee 118<br>80799 München</p>
  <span class="brand" style="right:14px;top:18px;font-size:5px">LORB</span>
  <i class="brand-sq" style="right:38px;top:19px;width:4px;height:4px"></i>
</div>

<!-- Reihe 7 -->
<div class="s" style="left:48px;top:2228px">
  <i class="box" style="left:0;top:10px;width:150px;height:90px"></i>
  <span class="hl w" style="left:14px;top:28px;font-size:5px">Gut beraten<br>mit der <b>LORB</b></span>
  <p class="pw" style="left:14px;top:44px;width:84px">Kurzer Text zur persönlichen Beratung durch unser erfahrenes Team.</p>
  <div class="ph" role="img" aria-label="Smartphone mit Website" style="left:114px;top:10px;width:54px;height:106px;border-radius:5px;background:linear-gradient(160deg,#f4f4f4,#c9c9c9);border:2px solid #222"></div>
  <i class="mk"></i><i class="ft"></i>
</div>
<div class="s" style="left:272px;top:2228px">
  <i style="left:0;top:0;width:134px;height:110px;background:#d9d9da"></i>
  <svg style="left:18px;top:16px" width="110" height="80" viewBox="0 0 110 80">
    <g stroke="#c4c4c4" stroke-width=".4"><line x1="0" y1="10" x2="110" y2="10"/><line x1="0" y1="30" x2="110" y2="30"/><line x1="0" y1="50" x2="110" y2="50"/><line x1="0" y1="70" x2="110" y2="70"/></g>
    <rect x="10" y="16" width="5" height="54" fill="#8a8a8a"/><rect x="16" y="42" width="5" height="28" fill="#2b2b2c"/><rect x="22" y="48" width="5" height="22" fill="#e8461e"/>
    <rect x="46" y="8" width="5" height="62" fill="#8a8a8a"/><rect x="52" y="30" width="5" height="40" fill="#2b2b2c"/><rect x="58" y="44" width="5" height="26" fill="#e8461e"/>
    <rect x="82" y="24" width="5" height="46" fill="#8a8a8a"/><rect x="88" y="36" width="5" height="34" fill="#2b2b2c"/><rect x="94" y="50" width="5" height="20" fill="#e8461e"/>
  </svg>
  <span class="hl o" style="left:142px;top:20px;font-size:5px">Analyse<br><b>Chart T1</b></span>
  <p class="p" style="left:142px;top:36px;width:58px">Kurzer Text zur Analyse der aktuellen Marktdaten.</p>
  <i class="mk"></i><i class="ft"></i>
</div>
<div class="s" style="left:496px;top:2228px">
  <div class="ph" role="img" aria-label="Drei Innenraumfotos" style="left:14px;top:0;width:184px;height:58px;background:linear-gradient(90deg,#c9c9c9,#8a7d6c 40%,#d8c3a8 70%,#6f5a45)"></div>
  <i class="box" style="left:0;top:66px;width:70px;height:24px"></i>
  <span class="hl o" style="left:6px;top:70px;font-size:5px">Immobilien<br><b>Wissen</b></span>
  <p class="p" style="left:80px;top:68px;width:110px">Kurzer Text mit Wissen rund um Kauf, Verkauf und Bewertung.</p>
  <i class="mk"></i><i class="ft"></i>
</div>
<div class="s" style="left:720px;top:2228px">
  <span class="hl" style="left:14px;top:14px;font-size:5px">Agenda <b>23 / 24</b></span>
  <i class="circle" style="left:14px;top:30px;width:30px;height:30px;background:var(--orange)"></i><span class="w" style="left:21px;top:42px;font-size:4.5px;font-weight:700">2017</span>
  <i class="circle" style="left:62px;top:34px;width:30px;height:30px;border:.5px solid #555"></i><span style="left:69px;top:46px;font-size:4.5px">2019</span>
  <i class="circle" style="left:108px;top:30px;width:30px;height:30px;background:var(--orange)"></i><span class="w" style="left:115px;top:42px;font-size:4.5px;font-weight:700">2020</span>
  <i class="circle" style="left:156px;top:34px;width:30px;height:30px;border:.5px solid #555"></i><span style="left:163px;top:46px;font-size:4.5px">2023</span>
  <p class="p" style="left:22px;top:82px;width:90px">Kurzer Text zur Agenda und zu den nächsten Schritten.</p>
  <i class="mk"></i><i class="ft"></i>
</div>

<!-- Reihe 8 -->
<div class="s" style="left:272px;top:2365px">
  <i style="left:0;top:0;width:134px;height:110px;background:#d9d9da"></i>
  <svg style="left:18px;top:24px" width="110" height="64" viewBox="0 0 110 64">
    <rect x="14" y="6" width="90" height="6" fill="#f2b3a0"/><rect x="14" y="6" width="66" height="6" fill="#e8461e"/>
    <rect x="14" y="26" width="90" height="6" fill="#f2b3a0"/><rect x="14" y="26" width="52" height="6" fill="#e8461e"/>
    <rect x="14" y="46" width="90" height="6" fill="#f2b3a0"/><rect x="14" y="46" width="78" height="6" fill="#e8461e"/>
  </svg>
  <span class="hl o" style="left:142px;top:20px;font-size:5px">Analyse<br><b>Chart T2</b></span>
  <p class="p" style="left:142px;top:36px;width:58px">Kurzer Text zur Analyse der aktuellen Marktdaten.</p>
  <i class="mk"></i><i class="ft"></i>
</div>
<div class="s" style="left:496px;top:2365px">
  <span class="hl" style="left:14px;top:16px;font-size:5px">Erfolgreich<br>vermarkten</span>
  <div class="ph" role="img" aria-label="Hände beim Unterschreiben eines Vertrags" style="left:6px;top:48px;width:66px;height:56px;background:linear-gradient(160deg,#cfcac4,#4a4440)"></div>
  <i style="left:62px;top:56px;width:12px;height:12px;background:var(--orange)"></i>
  <div class="ph" role="img" aria-label="Treppe im Wohnraum" style="left:86px;top:0;width:28px;height:56px;background:linear-gradient(160deg,#9a9a9a,#3f3f3f)"></div>
  <div class="ph" role="img" aria-label="Beraterin im hellen Raum" style="left:118px;top:0;width:80px;height:56px;background:linear-gradient(160deg,#e9e5e0,#b9aea2)"></div>
  <p class="p" style="left:90px;top:64px;width:50px">Kurzer Text zur Vermarktung.</p>
  <p class="p" style="left:148px;top:64px;width:50px">Kurzer Text zum Verkauf.</p>
  <i class="mk"></i><i class="ft"></i>
</div>

</body>
</html>
```